Etiketten-Design für nachhaltige Rasur- & Pflegeprodukte
> Wir suchen Verpackung und Etiketten für eine Marke für nachhaltige Rasur- & Pflegeprodukte.
Habedere liebe Designer,
„Habedere“ sagt man bei uns in Bayern, es bedeutet Hallo oder auf Wiedersehen, je nach Gelegenheit. In diesem Fall: Hallo.
Vielleicht kennst du uns schon, wir sind greenpines, wir betreiben einen kleinen Shop für Bartpflege & Rasur unter greenpines-shop.de und wir versuchen uns nun an einem neuen Thema: nachhaltige Rasur- & Pflegeprodukte für Frauen.
Das machen wir unter dem Namen „Sanft“.
Weil die Frage schon oft aufkam: Jawohl, wir haben uns dafür die Beine und die Achseln mit einem Rasierhobel rasiert.
> Zielgruppe.
Wir arbeiten an einer neuen Pflegelinie für Frauen, die sich vorwiegend mit der Rasur und den dazugehörigen Pflegeprodukten beschäftigt. Die Zielgruppe sind vor allem online-affine Frauen aus Deutschland, Österreich und der Schweiz, aber sicher auch europaweit im Alter von 21-45.
> Aufgabenstellung.
Wir sind auf der Suche nach einem Konzept für unsere Produktverpackungen bzw. Etiketten. Bei den Pflegeprodukten verzichten wir bewusst auf eine Umverpackung.
Konkret geplant sind ein Rasierhobel, dafür haben wir eine schöne Umverpackung. Außerdem starten wir mit Rasieröl, Rasierseife und einem After Shave Balsam. Es werden später noch andere Artikel dazukommen, eine Deocreme zum Beispiel.
Rasieröl, Rasiercreme und After Shave Balsam duften nach Orangen, es werden zwei oder drei weitere Duftrichtungen folgen, die eine wird beispielsweise nach Beeren duften, die andere nach Pfirsich und Mango – bitte beachte das bei der Erstellung des Konzeptes, die Unterschiede sollten später auf den ersten Blick erkennbar sein.
Zurück zum Thema Orange: Wir würden den Duft als leicht herben Zitrusduft bezeichnen.
> Die Maße.
• Umverpackung Rasierhobel, weißer Karton (165x90x40mm)
• Rasieröl 30ml (Etikett: 100x46mm)
• Rasiercreme 60ml (Etikett: 156x32mm)
• After Shave Balsam 60ml (Etikett: 156x32mm)
> Zwingend erforderliche Angaben.
Da es sich um Kosmetikprodukte handelt, sind einige Angaben auf dem Label zwingend erforderlich, beispielhaft sollen die folgenden Infos als Platzhalter dienen.
• Hergestellt für Friedrich Lautner e.K. von greenpines, Lindenhofweg 7, 83109 Kolbermoor
• Ingredients: Aqua, Stearic Acid, Cocos Nucifera oil, Glycerin, Potassium Hydroxide, Litsea Cubeba oil, (and) Citrus Sinensis Peel oil, Orbignya Oleifera oil, Sodium Hydroxide, Macadamia ternifolia oil, Talc, Kaolin, Citric Acid, Simmondsia chinensis oil, Maris sal, C.I. 77892 (and) Rad Clay, Citral, Limonene, Linalool, Geraniol
• Platz für einen Barcode
• Rasieröl sind 30ml / 1.01 FL.OZ. ODER Creme & Balsam jeweils 60ml / 2.03 FL. OZ.
Wir haben ein Bild der aktuellen Gefäße beigefügt, es kann aber durchaus sein, dass wir uns noch umen..

```html
<!DOCTYPE html>
<html lang="de">
<head>
<meta charset="utf-8">
<title>Sanft – Etiketten</title>
<link rel="stylesheet" href="https://fonts.googleapis.com/css2?family=Oswald:wght@300;400&display=swap">
<style>
  :root {
    --page: #ffffff;
    --label-left: #e6e6e3;
    --label-right: #fbfbfa;
    --edge: #b9bab6;
    --ink: #1f1f1f;
    --ink-soft: #333333;
    --sage: #7a9b8c;
    --peach: #e98a69;
    --peach-dark: #c5694a;
    --berry: #7d93be;
    --berry-dark: #5d729c;
    --citrus: #f4e6a8;
    --citrus-dark: #c9b56a;
    --rule: #9a9a96;
  }
  * { box-sizing: border-box; margin: 0; padding: 0; }
  html, body { width: 1200px; height: 848px; overflow: hidden; background: var(--page); }
  body { position: relative; font-family: "Oswald", "Arial Narrow", sans-serif; color: var(--ink); }

  .label {
    position: absolute;
    display: grid;
    grid-template-columns: var(--brand-w) 1fr;
    background: linear-gradient(90deg, var(--label-left) 0%, var(--label-right) 45%, #ffffff 100%);
    border-top: 2px solid var(--edge);
    border-bottom: 2px solid var(--edge);
    overflow: hidden;
  }
  .label--aftershave { left: 120px; top: 40px; width: 960px; height: 197px; --brand-w: 250px; --title: 40px; --band: 52px; --body: 17px; }
  .label--creme { left: 120px; top: 268px; width: 960px; height: 197px; --brand-w: 250px; --title: 40px; --band: 52px; --body: 17px; }
  .label--oil { left: 320px; top: 500px; width: 560px; height: 300px; --brand-w: 150px; --title: 30px; --band: 42px; --body: 14px; }

  .brand {
    display: flex; align-items: center; justify-content: center; gap: 12px;
  }
  .brand__dot { width: 44%; aspect-ratio: 1; border-radius: 50%; background: var(--sage); }
  .label--oil .brand__dot { width: 38%; }
  .brand__name { font-weight: 300; font-size: 26px; letter-spacing: 0.08em; color: var(--sage); }
  .label--oil .brand__name { font-size: 18px; }

  .content {
    border-left: 1px solid var(--rule);
    margin: 12px 0;
    padding: 0 0 0 12px;
    display: flex; flex-direction: column;
  }
  .title {
    font-weight: 400; font-size: var(--title); letter-spacing: 0.22em;
    text-align: right; padding-right: 40px; line-height: 1.6;
  }
  .label--oil .title { padding-right: 20px; }
  .variant {
    display: grid; grid-template-columns: calc(var(--band) * 0.9) 1fr calc(var(--band) * 0.9);
    height: var(--band); margin-left: -4px;
    background: var(--tone);
    border-top: 1px solid var(--tone-dark); border-bottom: 1px solid var(--tone-dark);
  }
  .variant--peach { --tone: var(--peach); --tone-dark: var(--peach-dark); }
  .variant--berry { --tone: var(--berry); --tone-dark: var(--berry-dark); }
  .variant--citrus { --tone: var(--citrus); --tone-dark: var(--citrus-dark); }
  .variant__no {
    display: flex; align-items: center; justify-content: center;
    border-right: 1px solid var(--tone-dark);
    font-size: calc(var(--band) * 0.34); writing-mode: vertical-rl; transform: rotate(180deg);
  }
  .variant__name {
    display: flex; align-items: center; justify-content: center;
    font-size: calc(var(--band) * 0.42); letter-spacing: 0.15em;
  }
  .variant__icon { border-left: 1px solid var(--tone-dark); background: var(--tone-dark); opacity: 0.45; }
  .desc {
    font-weight: 300; font-size: var(--body); line-height: 1.55; color: var(--ink-soft);
    padding: 8px 20px 0 4px;
  }
  .fineprint {
    margin-top: 10px; padding: 8px 16px 0 4px;
    border-top: 1px solid var(--rule);
    font-weight: 300; font-size: 11px; line-height: 1.65; color: var(--ink-soft);
  }
</style>
</head>
<body>

<section class="label label--aftershave">
  <div class="brand"><span class="brand__dot"></span><span class="brand__name">Sanft</span></div>
  <div class="content">
    <h2 class="title">AFTER SHAVE</h2>
    <div class="variant variant--peach">
      <span class="variant__no">№ 4</span>
      <span class="variant__name">PFIRSICH-MANGO</span>
      <span class="variant__icon" role="img" aria-label="Strichzeichnung Pfirsich und Mango"></span>
    </div>
    <p class="desc">Blidtext Pflegt und beruhigt deine Haut während der Rasur<br>und sprendet extra viel Feuchtigkeit Blindtext</p>
  </div>
</section>

<section class="label label--creme">
  <div class="brand"><span class="brand__dot"></span><span class="brand__name">Sanft</span></div>
  <div class="content">
    <h2 class="title">RASIERCREME</h2>
    <div class="variant variant--citrus">
      <span class="variant__no">№ 3</span>
      <span class="variant__name">ORANGE-ZITRUS</span>
      <span class="variant__icon" role="img" aria-label="Strichzeichnung Zitrusscheibe"></span>
    </div>
    <p class="desc">Blidtext Pflegt und beruhigt deine Haut während der Rasur<br>und sprendet extra viel Feuchtigkeit Blindtext</p>
  </div>
</section>

<section class="label label--oil">
  <div class="brand"><span class="brand__dot"></span><span class="brand__name">Sanft</span></div>
  <div class="content">
    <h2 class="title">RASIERÖL</h2>
    <div class="variant variant--berry">
      <span class="variant__no">№ 5</span>
      <span class="variant__name">BEERE</span>
      <span class="variant__icon" role="img" aria-label="Strichzeichnung Beeren"></span>
    </div>
    <p class="desc">Blidtext Pflegt und beruhigt deine Haut während der<br>Rasur und sprendet extra viel Feuchtigkeit Blindtext</p>
    <p class="fineprint">Mit Mandelöl und Jojobaöl für eine glatte, sanfte Rasur ohne Reizungen, ohne Parabene,<br>vegan hergestellt in kleinen Chargen, frei von Mikroplastik, schonend für empfindliche Haut,<br>einige Tropfen auf die feuchte Haut geben und sanft einmassieren. Vor Kindern geschützt<br>aufbewahren, kühl und trocken lagern</p>
  </div>
</section>

</body>
</html>
```